Brightway Haul & Upkeep Services, are a company that offers a 'one stop shop' pre-move clean up a

I have already selected a logo which I would like on the front of the business cards along with phone numbers, web address and email which are:
0487650392
www.brightwayhaul.com.au
brightwayhaulandupkeep@mailbox.example

On the back of the card I would like to list some of the types of service we offer (clean - move - repairs/maintenance) which are:
CLEAN - windows, gutters, solar panels, driveways/paths, carpets.
MOVE - Small/medium size house/office moves, large item pick-up & delivery, yard clean-up and removal.
General maintenance and repairs.

I would like the blue logo on a gray background.

Thanks

```html
<!DOCTYPE html>
<html lang="en">
<head>
<meta charset="utf-8">
<title>Brightway Haul &amp; Upkeep Services – Business Card</title>
<link rel="stylesheet" href="https://fonts.googleapis.com/css2?family=Open+Sans:wght@400;600;800&display=swap">
<style>
  :root {
    --brand-blue: #2d72c2;
    --brand-blue-dark: #235ea3;
    --card-grey-light: #f0f0f1;
    --card-grey-mid: #d3d3d5;
    --card-grey-dark: #b4b4b7;
    --swoosh: #1f1f22;
    --ink: #2a2a2c;
    --white: #ffffff;
    --page: #e6e4e1;
  }
  * { box-sizing: border-box; margin: 0; padding: 0; }
  html, body {
    width: 1200px; height: 764px; overflow: hidden;
    background: var(--page);
    font-family: "Open Sans", Arial, sans-serif;
  }
  .sheet {
    width: 1200px; height: 764px;
    display: flex; align-items: center; justify-content: center; gap: 40px;
  }
  .card {
    position: relative;
    width: 540px; height: 330px;
    border-radius: 22px;
    overflow: hidden;
    background: linear-gradient(160deg, var(--card-grey-light) 0%, var(--card-grey-mid) 55%, var(--card-grey-dark) 100%);
    box-shadow: 0 10px 24px rgba(0,0,0,0.18);
  }
  .card__shapes { position: absolute; inset: 0; width: 100%; height: 100%; }
  .card__shapes .band { fill: var(--brand-blue); }
  .card__shapes .swoosh { fill: var(--swoosh); }

  .brand-name {
    font-weight: 800;
    color: var(--brand-blue);
    text-transform: uppercase;
    line-height: 1.05;
    letter-spacing: 0.5px;
  }

  /* Front */
  .card--front .brand-name {
    position: absolute; left: 48px; top: 52px;
    font-size: 34px;
  }
  .contact {
    position: absolute; left: 0; right: 0; bottom: 34px;
    display: flex; align-items: center; justify-content: flex-end;
    padding-right: 34px;
    color: var(--white);
    font-size: 13px;
  }
  .contact__phone { display: flex; align-items: center; gap: 6px; }
  .contact__divider {
    width: 1px; height: 44px; background: var(--white);
    margin: 0 16px;
  }
  .contact__lines { display: flex; flex-direction: column; gap: 8px; }
  .contact__line { display: flex; align-items: center; gap: 7px; }
  .icon { width: 13px; height: 13px; flex: none; }
  .icon path, .icon circle, .icon rect { fill: none; stroke: var(--white); stroke-width: 1.6; }

  /* Back */
  .card--back .brand-name {
    position: absolute; left: 0; right: 0; top: 58px;
    text-align: center;
    font-size: 36px;
  }
  .services {
    position: absolute; left: 0; right: 0; top: 176px;
    text-align: center;
    color: var(--ink);
  }
  .services__title {
    color: var(--brand-blue);
    font-weight: 600;
    font-size: 20px;
    letter-spacing: 7px;
    margin-bottom: 10px;
  }
  .services__list { list-style: none; font-size: 18px; font-weight: 600; line-height: 1.45; }
  .services__list li span + span { margin-left: 22px; }
</style>
</head>
<body>
<main class="sheet">

  <section class="card card--front" aria-label="Card front">
    <svg class="card__shapes" viewBox="0 0 540 330" preserveAspectRatio="none" aria-hidden="true">
      <path class="band" d="M0,205 C170,250 390,215 540,115 L540,330 L0,330 Z"/>
      <path class="swoosh" d="M40,190 C210,232 400,198 525,118 C410,212 210,246 40,190 Z"/>
    </svg>
    <h1 class="brand-name">Brightway Haul<br>&amp; Upkeep Services</h1>
    <div class="contact">
      <div class="contact__phone">
        <svg class="icon" viewBox="0 0 16 16" aria-hidden="true">
          <path d="M4 1.5 L6.5 4.5 L5 6.5 C6 8.5 7.5 10 9.5 11 L11.5 9.5 L14.5 12 L13 14.5 C7 14 2 9 1.5 3 Z"/>
        </svg>
        <span>0487650392</span>
      </div>
      <div class="contact__divider"></div>
      <div class="contact__lines">
        <div class="contact__line">
          <svg class="icon" viewBox="0 0 16 16" aria-hidden="true">
            <rect x="1.5" y="3.5" width="13" height="9" rx="1"/>
            <path d="M1.5 4 L8 9 L14.5 4"/>
          </svg>
          <span>brightwayhaulandupkeep@mailbox.example</span>
        </div>
        <div class="contact__line">
          <svg class="icon" viewBox="0 0 16 16" aria-hidden="true">
            <circle cx="8" cy="8" r="6.5"/>
            <path d="M1.5 8 H14.5 M8 1.5 C5 5 5 11 8 14.5 M8 1.5 C11 5 11 11 8 14.5"/>
          </svg>
          <span>www.brightwayhaul.com.au</span>
        </div>
      </div>
    </div>
  </section>

  <section class="card card--back" aria-label="Card back">
    <h2 class="brand-name">Brightway Haul<br>&amp; Upkeep Services</h2>
    <div class="services">
      <p class="services__title">Services we offer</p>
      <ul class="services__list">
        <li><span>• Clean</span><span>• Move</span></li>
        <li>• General maintenance and repairs.</li>
      </ul>
    </div>
  </section>

</main>
</body>
</html>
```